I need a label design to go on our jars of honey. Our company is called Marrowdale Honey Co. The type of honey is called Fernlight Glen Honey. The jars are 1kg. Attached is the label size. Left hand side needs to have nutritional info... as attached. Middle section is our company name, honey type, 1kg & Whangamata, NZ. Right hand side needs to have info as per photo (raw honey etc). I would like to upload more pictures... but I’m unsure how to do this? Thanks, Carla

Target Market(s)

Honey consumers... families

Industry/Entity Type

Food Production

Colors

Designer to choose colors to be used in the design.

Requirements
Must have
• Nutritional info as per upload
• Type of honey & company name as per upload
• 1kg
• Address
Nice to have
• Similar fonts to upload.
• Possibly background image... floral or beach... very faint though.

```html
<!DOCTYPE html>
<html lang="en">
<head>
<meta charset="utf-8">
<title>Marrowdale Honey Co. — Fernlight Glen Honey Label</title>
<link href="https://fonts.googleapis.com/css2?family=Amatic+SC:wght@700&family=Montserrat:wght@300;400&family=Nothing+You+Could+Do&family=Roboto:ital,wght@0,400;1,400&display=swap" rel="stylesheet">
<style>
  :root {
    --backdrop: #262b2d;
    --label-base: #ebe5e3;
    --bloom-white: #f7f6ef;
    --bloom-grey: #c9cbc6;
    --bloom-blush: #efe3e1;
    --ink: #141414;
    --rule: #1d1d1d;
    --table-line: #3a3a3a;
  }
  * { box-sizing: border-box; margin: 0; padding: 0; }
  html, body { width: 1200px; height: 1200px; overflow: hidden; }
  body {
    background: var(--backdrop);
    display: flex;
    align-items: center;
    justify-content: center;
    font-family: "Roboto", sans-serif;
    color: var(--ink);
  }
  .label {
    position: relative;
    width: 1140px;
    height: 520px;
    background: var(--label-base);
    overflow: hidden;
  }
  .label__floral {
    position: absolute;
    inset: 0;
    background:
      radial-gradient(circle at 52% 22%, var(--bloom-white) 0, rgba(247,246,239,0.7) 9%, transparent 20%),
      radial-gradient(circle at 72% 68%, var(--bloom-white) 0, rgba(247,246,239,0.75) 10%, transparent 22%),
      radial-gradient(circle at 30% 70%, var(--bloom-white) 0, rgba(247,246,239,0.6) 10%, transparent 22%),
      radial-gradient(ellipse at 60% 60%, var(--bloom-grey) 0, transparent 45%),
      linear-gradient(180deg, var(--bloom-blush), var(--label-base) 60%, #e4e2de);
  }
  .panel { position: absolute; top: 0; bottom: 0; }
  .panel--nutrition { left: 30px; width: 290px; }
  .panel--brand { left: 300px; width: 540px; text-align: center; }
  .panel--info { left: 850px; width: 260px; }

  .nutrition-table {
    margin-top: 44px;
    width: 270px;
    border: 1.5px solid var(--table-line);
    font-size: 11px;
    line-height: 1.35;
    background: rgba(255,255,255,0.35);
  }
  .nutrition-table__title { font-size: 14px; padding: 8px 10px 4px; border-bottom: 1px solid var(--table-line); }
  .nutrition-table__meta { padding: 6px 10px; border-bottom: 1px solid var(--table-line); }
  .nutrition-table table { width: 100%; border-collapse: collapse; }
  .nutrition-table th, .nutrition-table td { padding: 5px 8px; text-align: right; font-weight: 400; }
  .nutrition-table th:first-child, .nutrition-table td:first-child { text-align: left; }
  .nutrition-table thead th { border-bottom: 1px solid var(--table-line); font-size: 10px; }
  .nutrition-table tbody tr:last-child td { padding-bottom: 16px; }
  .nutrition-note {
    margin-top: 10px;
    font-style: italic;
    font-size: 15px;
    line-height: 1.4;
  }

  .brand-company {
    margin-top: 52px;
    font-family: "Amatic SC", cursive;
    font-weight: 700;
    font-size: 30px;
    line-height: 1.2;
    letter-spacing: 0.36em;
    text-transform: uppercase;
    white-space: nowrap;
  }
  .brand-variety {
    margin-top: 112px;
    font-family: "Montserrat", sans-serif;
    font-weight: 300;
    font-size: 30px;
    line-height: 1.2;
    letter-spacing: 0.4em;
    padding-left: 0.4em;
  }
  .brand-name {
    margin-top: -4px;
    font-family: "Nothing You Could Do", cursive;
    font-weight: 400;
    font-size: 70px;
    line-height: 1.2;
  }
  .brand-weight {
    margin-top: 20px;
    font-family: "Amatic SC", cursive;
    font-weight: 700;
    font-size: 32px;
    line-height: 1.2;
  }
  .brand-rule { width: 36px; height: 3px; background: var(--rule); margin: 8px auto 12px; }
  .brand-origin {
    font-family: "Amatic SC", cursive;
    font-weight: 700;
    font-size: 34px;
    line-height: 1.2;
    letter-spacing: 0.14em;
    text-transform: uppercase;
    white-space: nowrap;
  }

  .info-list {
    margin-top: 130px;
    list-style: none;
    font-size: 15px;
    line-height: 1.5;
  }
  .info-list li + li { margin-top: 18px; }
</style>
</head>
<body>
  <div class="label">
    <div class="label__floral" role="img" aria-label="Very faint photograph of white blossoms across the label"></div>

    <section class="panel panel--nutrition">
      <div class="nutrition-table">
        <div class="nutrition-table__title">Nutrition Information</div>
        <div class="nutrition-table__meta">Servings per package: 50<br>Serving size: 20g</div>
        <table>
          <thead>
            <tr><th>Quantity per serving</th><th></th><th>per 100g</th></tr>
          </thead>
          <tbody>
            <tr><td>Energy</td><td>272kJ</td><td>1360kJ</td></tr>
            <tr><td>Protein</td><td>0.1g</td><td>0.4g</td></tr>
            <tr><td>Fat, total</td><td>0g</td><td>0g</td></tr>
            <tr><td>Carbohydrate</td><td>16.2g</td><td>81g</td></tr>
            <tr><td>– sugars</td><td>16.0g</td><td>80g</td></tr>
            <tr><td>Sodium</td><td>2mg</td><td>10mg</td></tr>
          </tbody>
        </table>
      </div>
      <p class="nutrition-note">Warm gently when needed.<br>Best within 12 months.</p>
    </section>

    <section class="panel panel--brand">
      <p class="brand-company">Marrowdale Honey Co.</p>
      <p class="brand-variety">FERNLIGHT</p>
      <h1 class="brand-name">Glen Honey</h1>
      <p class="brand-weight">1kg</p>
      <div class="brand-rule"></div>
      <p class="brand-origin">Kauriwai Bay, N.Z.</p>
    </section>

    <section class="panel panel--info">
      <ul class="info-list">
        <li>Pure raw honey, unheated and unfiltered.</li>
        <li>Produced by our own hives.</li>
        <li>Store in a cool dry place.</li>
        <li>Product of New Zealand.</li>
      </ul>
    </section>
  </div>
</body>
</html>
```